Powerpoint template

I am looking for a brand based PPT template that can also be used as the basis for datasheet creation. I have attached a document with some of our branding structure in as an FYI to help.

To be clear I am looking a background design, bullets, layouts, different styles for differing content types. This is a template to be used for lots of presentations.

Reason: I have committed to the payment and wanted to give people chance to respond.

Target Market(s)

Enterprise

Requirements
Must have
• Brand standard. different page design choices for different content types
Nice to have
• brand font if it works. Use of some play on the logo in bullets
Should not have
• must be on brand and focused on the business audience

```html
<!DOCTYPE html>
<html lang="en">
<head>
<meta charset="utf-8">
<title>Quantrel Presentation Template – Layouts</title>
<link rel="stylesheet" href="https://fonts.googleapis.com/css2?family=Carlito:wght@400;700&family=Open+Sans:wght@400;600;700&display=swap">
<style>
  :root {
    --stage: #000000;
    --paper: #ffffff;
    --green: #7ab53a;
    --navy: #12375f;
    --navy-deep: #0c2c52;
    --blue-light: #2a78ad;
    --gold: #b8860b;
    --gold-text: #a8800f;
    --ink: #4d4d45;
    --ink-dark: #2a2a2a;
    --olive: #6b6a4c;
    --row-light: #efeee6;
    --row-dark: #d6d4c4;
    --rule: #d9d9d9;
    --footer-text: #ffffff;
  }
  * { box-sizing: border-box; margin: 0; padding: 0; }
  html, body { width: 1200px; height: 1000px; overflow: hidden; background: var(--stage); }
  body { position: relative; font-family: "Carlito", "Open Sans", sans-serif; }

  .slide {
    position: absolute; width: 500px; height: 375px;
    background: var(--paper); overflow: hidden;
  }
  .slide--layout-quote  { left: 64px;  top: 67px; }
  .slide--layout-lists  { left: 625px; top: 67px; }
  .slide--layout-text-table { left: 64px;  top: 526px; }
  .slide--layout-table-text { left: 625px; top: 526px; }

  .slide__title {
    position: absolute; left: 34px; top: 18px;
    font-family: "Carlito", sans-serif; font-weight: 700;
    font-size: 29px; color: var(--green); letter-spacing: 0.2px;
  }
  .slide__rule {
    position: absolute; left: 50px; top: 64px; width: 400px; height: 6px;
    background: radial-gradient(ellipse at center top, rgba(0,0,0,0.14), rgba(0,0,0,0) 70%);
  }

  /* Footer */
  .footer { position: absolute; left: 0; top: 0; width: 500px; height: 375px; pointer-events: none; }
  .footer__wave { position: absolute; left: 0; top: 0; }
  .footer__address {
    position: absolute; left: 19px; top: 333px;
    font-family: "Open Sans", sans-serif; font-size: 6px; line-height: 8px; color: var(--footer-text);
  }
  .footer__link {
    position: absolute; display: flex; align-items: center; gap: 6px;
    font-family: "Open Sans", sans-serif; font-size: 6px; color: var(--footer-text);
  }
  .footer__link .dot {
    width: 13px; height: 13px; border-radius: 50%;
    background: #e8eef4; display: flex; align-items: center; justify-content: center;
  }
  .footer__link .dot svg { width: 8px; height: 8px; }
  .footer__link--web   { left: 265px; top: 307px; }
  .footer__link--page  { left: 114px; top: 334px; }
  .footer__link--chirp { left: 265px; top: 332px; }
  .footer__link--mail  { left: 114px; top: 359px; }
  .footer__link--video { left: 265px; top: 357px; }
  .footer__brand {
    position: absolute; left: 380px; top: 303px; display: flex; align-items: center; gap: 5px;
    font-family: "Carlito", sans-serif; font-size: 21px; color: var(--footer-text);
  }
  .footer__brand .mark { width: 13px; height: 13px; border-radius: 50%; background: var(--footer-text); }
  .pager {
    position: absolute; left: 383px; top: 341px; display: flex; align-items: center; gap: 8px;
    font-family: "Open Sans", sans-serif; font-size: 8px; color: var(--footer-text);
  }
  .pager__btn {
    width: 17px; height: 11px; border-radius: 6px;
    background: linear-gradient(#33597f, #0b2440); border: 1px solid #4d7296;
    display: flex; align-items: center; justify-content: center;
  }
  .pager__btn svg { width: 6px; height: 6px; }
  .pager__of { font-style: italic; font-weight: 700; margin: 0 3px; }

  /* Body text */
  .body-text {
    position: absolute; left: 34px; width: 433px;
    font-family: "Open Sans", sans-serif; font-size: 9.2px; line-height: 13.5px;
    color: var(--ink); text-align: justify;
  }
  .body-text--indent { text-indent: 20px; }

  /* Quote slide */
  .pull-quote {
    position: absolute; left: 34px; top: 86px; width: 434px;
    font-family: "Open Sans", sans-serif; font-weight: 700; font-size: 18.5px; line-height: 26.5px;
    color: #4f4f45; text-transform: uppercase; text-align: justify; text-align-last: justify;
  }
  .pull-quote__end {
    position: absolute; left: 455px; top: 146px; width: 18px; height: 18px; border-radius: 50%;
    background: linear-gradient(#ffffff, #d6dde4); border: 1px solid #b9c4cf;
    display: flex; align-items: center; justify-content: center;
  }
  .pull-quote__end svg { width: 10px; height: 10px; }
  .author-badge {
    display: inline-flex; width: 12px; height: 12px; border-radius: 50%;
    background: linear-gradient(#ffffff, #cfd7df); border: 1px solid #b9c4cf;
    vertical-align: -2px; margin-right: 3px; align-items: center; justify-content: center;
  }
  .author-badge svg { width: 7px; height: 7px; }

  /* Bullet lists slide */
  .list-col { position: absolute; top: 83px; }
  .list-col--tick  { left: 30px; }
  .list-col--point { left: 183px; }
  .list-col--arrow { left: 333px; }
  .list-col__head {
    display: flex; align-items: center; gap: 6px;
    font-family: "Open Sans", sans-serif; font-weight: 600; font-size: 11.5px; color: #3e3e3e;
    margin-bottom: 17px;
  }
  .list-col__badge {
    width: 19px; height: 19px; border-radius: 50%;
    background: linear-gradient(#ffffff, #d4dbe2); border: 1px solid #b9c4cf;
    display: flex; align-items: center; justify-content: center;
  }
  .list-col__badge svg { width: 11px; height: 11px; }
  .list { list-style: none; }
  .list li {
    display: flex; align-items: center; gap: 6px; height: 20.7px;
    font-family: "Open Sans", sans-serif; font-weight: 700; font-size: 9.3px;
  }
  .list li svg { width: 8px; height: 8px; flex: none; }
  .list--tick  li { color: var(--navy); margin-left: 3px; }
  .list--point li { color: var(--gold-text); margin-left: 3px; }
  .list--arrow li { color: var(--ink-dark); margin-left: 3px; }

  /* Comparison table */
  .compare {
    position: absolute; width: 434px; border-collapse: collapse; table-layout: fixed;
    font-family: "Open Sans", sans-serif;
  }
  .compare th {
    background: var(--navy-deep); color: #fff; font-weight: 700; font-size: 10.5px;
    text-align: left; height: 20px; padding: 0 5px;
    border-left: 1px solid #ffffff;
  }
  .compare th:first-child { border-left: none; }
  .compare th.is-featured { background: var(--gold); }
  .compare td {
    height: 16.5px; padding: 0 5px; font-size: 8.5px; color: var(--olive);
    border-left: 1px solid #ffffff;
  }
  .compare td:first-child { border-left: none; }
  .compare tr:nth-child(odd) td { background: var(--row-light); }
  .compare tr:nth-child(even) td { background: var(--row-dark); }
  .compare td.is-featured { box-shadow: inset 0 0 0 200px rgba(0,0,0,0.025); }
  .compare td svg { width: 8px; height: 8px; vertical-align: -1px; margin-right: 4px; }
  .slide--layout-text-table .compare { left: 28px; top: 173px; }
  .slide--layout-table-text .compare { left: 34px; top: 89px; }
</style>
</head>
<body>

<svg width="0" height="0" style="position:absolute" aria-hidden="true">
  <defs>
    <symbol id="icon-tick" viewBox="0 0 10 10"><path d="M1 5.3 L3.8 8 L9 1.8" fill="none" stroke="currentColor" stroke-width="1.9"/></symbol>
    <symbol id="icon-dot" viewBox="0 0 10 10"><circle cx="5" cy="5" r="3.4" fill="currentColor"/></symbol>
    <symbol id="icon-arrow-right" viewBox="0 0 10 10"><path d="M0.5 3.6 H5 V1 L9.5 5 L5 9 V6.4 H0.5 Z" fill="currentColor"/></symbol>
    <symbol id="icon-arrow-left" viewBox="0 0 10 10"><path d="M9.5 3.6 H5 V1 L0.5 5 L5 9 V6.4 H9.5 Z" fill="currentColor"/></symbol>
    <symbol id="icon-caret-left" viewBox="0 0 10 10"><path d="M7 1 L3 5 L7 9" fill="none" stroke="currentColor" stroke-width="2"/></symbol>
    <symbol id="icon-caret-right" viewBox="0 0 10 10"><path d="M3 1 L7 5 L3 9" fill="none" stroke="currentColor" stroke-width="2"/></symbol>
    <symbol id="icon-home" viewBox="0 0 10 10"><path d="M5 1 L9.5 5 H8 V9 H6 V6.5 H4 V9 H2 V5 H0.5 Z" fill="currentColor"/></symbol>
    <symbol id="icon-at" viewBox="0 0 10 10"><circle cx="5" cy="5" r="1.8" fill="none" stroke="currentColor" stroke-width="1.2"/><path d="M6.8 3.5 V6 Q6.8 7 7.8 7 Q9 7 9 5 A4 4 0 1 0 7 8.5" fill="none" stroke="currentColor" stroke-width="1.2"/></symbol>
    <symbol id="icon-user" viewBox="0 0 10 10"><circle cx="5" cy="3.2" r="2.2" fill="currentColor"/><path d="M1 9.5 Q1 5.8 5 5.8 Q9 5.8 9 9.5 Z" fill="currentColor"/></symbol>
    <linearGradient id="footer-blue" x1="0" y1="1" x2="1" y2="0">
      <stop offset="0" stop-color="#0b2a4d"/>
      <stop offset="0.55" stop-color="#123f6c"/>
      <stop offset="1" stop-color="#2a78ad"/>
    </linearGradient>
    <symbol id="footer-wave" viewBox="0 0 500 375">
      <path d="M0 304 C90 322 170 318 260 296 C340 276 420 262 500 266 L500 375 L0 375 Z" fill="url(#footer-blue)"/>
      <path d="M0 304 C90 322 170 318 260 296 C340 276 420 262 500 266" fill="none" stroke="#4d8fc0" stroke-width="1.2" opacity="0.7"/>
    </symbol>
  </defs>
</svg>

<!-- Slide 5: quote layout -->
<section class="slide slide--layout-quote">
  <h1 class="slide__title">One Column Example</h1>
  <div class="slide__rule"></div>
  <p class="pull-quote">”At vero eos et accusam et justo duo dolores ea rebum stet kasd guber vero eos et accusam kasd guber rebum stet”</p>
  <span class="pull-quote__end" style="color:var(--navy)"><svg><use href="#icon-arrow-left"/></svg></span>
  <p class="body-text" style="top:186px"><span class="author-badge" style="color:var(--navy)"><svg><use href="#icon-user"/></svg></span>Lorem ipsum dolor sit amet, consetetur sadipscing elitr, sed diam nonumy eirmod tempor invidunt ut labore et dolore magna aliquyam erat, sed diam voluptua. Stet clita kasd gubergren, no sea takimata sanctus est Lorem ipsum dolor sit amet.</p>
  <p class="body-text" style="top:242px">At vero eos et accusam et justo duo dolores et ea rebum. Stet clita kasd gubergren, no sea takimata. Stet clita kasd gubergren, no sea takimata sanctus est Lorem ipsum dolor sit amet.</p>
  <footer class="footer">
    <svg class="footer__wave" width="500" height="375"><use href="#footer-wave"/></svg>
    <p class="footer__address">Lorem Ipsum Street 122<br>State, Country<br>Phone&nbsp; 0123 4567 89</p>
    <span class="footer__link footer__link--web"><span class="dot" style="color:var(--navy)"><svg><use href="#icon-home"/></svg></span>company-name.com</span>
    <span class="footer__link footer__link--page"><span class="dot"></span>linkpage.net/company-name</span>
    <span class="footer__link footer__link--chirp"><span class="dot"></span>chirpnet.net/company-name</span>
    <span class="footer__link footer__link--mail"><span class="dot" style="color:var(--navy)"><svg><use href="#icon-at"/></svg></span>hello@company-name.com</span>
    <span class="footer__link footer__link--video"><span class="dot"></span>vidhub.net/company-name</span>
    <div class="footer__brand"><span class="mark"></span>quantrel</div>
    <div class="pager"><span class="pager__btn" style="color:#fff"><svg><use href="#icon-caret-left"/></svg></span><span>5 <span class="pager__of">of</span> 13</span><span class="pager__btn" style="color:#fff"><svg><use href="#icon-caret-right"/></svg></span></div>
  </footer>
</section>

<!-- Slide 6: bullet lists -->
<section class="slide slide--layout-lists">
  <h1 class="slide__title">Bullet Lists</h1>
  <div class="slide__rule"></div>
  <div class="list-col list-col--tick">
    <div class="list-col__head"><span class="list-col__badge" style="color:var(--navy)"><svg><use href="#icon-tick"/></svg></span>Tick List Example</div>
    <ul class="list list--tick">
      <li><svg><use href="#icon-tick"/></svg>Stet clita kasd gubergren</li>
      <li><svg><use href="#icon-tick"/></svg>sea takimata sanctus</li>
      <li><svg><use href="#icon-tick"/></svg>dolor sit amet</li>
      <li><svg><use href="#icon-tick"/></svg>Consetetur labore</li>
      <li><svg><use href="#icon-tick"/></svg>et dolore dolores</li>
      <li><svg><use href="#icon-tick"/></svg>et ea rebum</li>
    </ul>
  </div>
  <div class="list-col list-col--point">
    <div class="list-col__head"><span class="list-col__badge" style="color:var(--navy)"><svg><use href="#icon-dot"/></svg></span>Point List Example</div>
    <ul class="list list--point">
      <li><svg style="color:var(--navy)"><use href="#icon-dot"/></svg>Stet clita kasd gubergren</li>
      <li><svg style="color:var(--navy)"><use href="#icon-dot"/></svg>sea takimata sanctus</li>
      <li><svg style="color:var(--navy)"><use href="#icon-dot"/></svg>est Lorem ipsum</li>
      <li><svg style="color:var(--navy)"><use href="#icon-dot"/></svg>dolor sit amet</li>
      <li><svg style="color:var(--navy)"><use href="#icon-dot"/></svg>Consetetur labore</li>
      <li><svg style="color:var(--navy)"><use href="#icon-dot"/></svg>et dolore dolores</li>
      <li><svg style="color:var(--navy)"><use href="#icon-dot"/></svg>et ea rebum</li>
    </ul>
  </div>
  <div class="list-col list-col--arrow">
    <div class="list-col__head"><span class="list-col__badge" style="color:var(--navy)"><svg><use href="#icon-arrow-right"/></svg></span>Arrow List Example</div>
    <ul class="list list--arrow">
      <li><svg style="color:var(--navy)"><use href="#icon-arrow-right"/></svg>est Lorem ipsum</li>
      <li><svg style="color:var(--navy)"><use href="#icon-arrow-right"/></svg>dolor sit amet</li>
      <li><svg style="color:var(--navy)"><use href="#icon-arrow-right"/></svg>Consetetur labore</li>
      <li><svg style="color:var(--navy)"><use href="#icon-arrow-right"/></svg>et dolore dolores</li>
      <li><svg style="color:var(--navy)"><use href="#icon-arrow-right"/></svg>et ea rebum</li>
    </ul>
  </div>
  <footer class="footer">
    <svg class="footer__wave" width="500" height="375"><use href="#footer-wave"/></svg>
    <p class="footer__address">Lorem Ipsum Street 122<br>State, Country<br>Phone&nbsp; 0123 4567 89</p>
    <span class="footer__link footer__link--web"><span class="dot" style="color:var(--navy)"><svg><use href="#icon-home"/></svg></span>company-name.com</span>
    <span class="footer__link footer__link--page"><span class="dot"></span>linkpage.net/company-name</span>
    <span class="footer__link footer__link--chirp"><span class="dot"></span>chirpnet.net/company-name</span>
    <span class="footer__link footer__link--mail"><span class="dot" style="color:var(--navy)"><svg><use href="#icon-at"/></svg></span>hello@company-name.com</span>
    <span class="footer__link footer__link--video"><span class="dot"></span>vidhub.net/company-name</span>
    <div class="footer__brand"><span class="mark"></span>quantrel</div>
    <div class="pager"><span class="pager__btn" style="color:#fff"><svg><use href="#icon-caret-left"/></svg></span><span>6 <span class="pager__of">of</span> 13</span><span class="pager__btn" style="color:#fff"><svg><use href="#icon-caret-right"/></svg></span></div>
  </footer>
</section>

<!-- Slide 7: text above table -->
<section class="slide slide--layout-text-table">
  <h1 class="slide__title">One Column and Table</h1>
  <div class="slide__rule"></div>
  <p class="body-text body-text--indent" style="top:85px">Lorem ipsum dolor sit amet, consetetur sadipscing elitr, sed diam nonumy eirmod tempor invidunt ut labore et dolore magna aliquyam erat, sed diam voluptua. Stet clita kasd gubergren, no sea takimata sanctus est Lorem ipsum dolor sit amet.</p>
  <p class="body-text" style="top:139px">At vero eos et accusam et justo duo dolores et ea rebum. Stet clita kasd gubergren, no sea takimata. Stet clita kasd gubergren, no sea takimata sanctus est Lorem ipsum dolor sit amet.</p>
  <table class="compare">
    <thead><tr><th>Navigo</th><th>Lumen</th><th>Orbit</th></tr></thead>
    <tbody>
      <tr><td><svg style="color:var(--navy)"><use href="#icon-tick"/></svg>Lorem ipsum dolor</td><td><svg style="color:var(--navy)"><use href="#icon-tick"/></svg>Lorem ipsum dolor</td><td></td></tr>
      <tr><td></td><td><svg style="color:var(--navy)"><use href="#icon-tick"/></svg>Lorem ipsum dolor</td><td><svg style="color:var(--navy)"><use href="#icon-tick"/></svg>Lorem ipsum dolor</td></tr>
      <tr><td><svg style="color:var(--navy)"><use href="#icon-tick"/></svg>Lorem ipsum dolor</td><td><svg style="color:var(--navy)"><use href="#icon-tick"/></svg>Lorem ipsum dolor</td><td><svg style="color:var(--navy)"><use href="#icon-tick"/></svg>Lorem ipsum dolor</td></tr>
      <tr><td></td><td><svg style="color:var(--navy)"><use href="#icon-tick"/></svg>Lorem ipsum dolor</td><td></td></tr>
    </tbody>
  </table>
  <footer class="footer">
    <svg class="footer__wave" width="500" height="375"><use href="#footer-wave"/></svg>
    <p class="footer__address">Lorem Ipsum Street 122<br>State, Country<br>Phone&nbsp; 0123 4567 89</p>
    <span class="footer__link footer__link--web"><span class="dot" style="color:var(--navy)"><svg><use href="#icon-home"/></svg></span>company-name.com</span>
    <span class="footer__link footer__link--page"><span class="dot"></span>linkpage.net/company-name</span>
    <span class="footer__link footer__link--chirp"><span class="dot"></span>chirpnet.net/company-name</span>
    <span class="footer__link footer__link--mail"><span class="dot" style="color:var(--navy)"><svg><use href="#icon-at"/></svg></span>hello@company-name.com</span>
    <span class="footer__link footer__link--video"><span class="dot"></span>vidhub.net/company-name</span>
    <div class="footer__brand"><span class="mark"></span>quantrel</div>
    <div class="pager"><span class="pager__btn" style="color:#fff"><svg><use href="#icon-caret-left"/></svg></span><span>7 <span class="pager__of">of</span> 13</span><span class="pager__btn" style="color:#fff"><svg><use href="#icon-caret-right"/></svg></span></div>
  </footer>
</section>

<!-- Slide 8: table above text -->
<section class="slide slide--layout-table-text">
  <h1 class="slide__title">One Column and Table</h1>
  <div class="slide__rule"></div>
  <table class="compare">
    <thead><tr><th>Navigo</th><th class="is-featured">Lumen</th><th>Orbit</th></tr></thead>
    <tbody>
      <tr><td><svg style="color:var(--navy)"><use href="#icon-tick"/></svg>Lorem ipsum dolor</td><td class="is-featured"><svg style="color:var(--navy)"><use href="#icon-tick"/></svg>Lorem ipsum dolor</td><td></td></tr>
      <tr><td></td><td class="is-featured"><svg style="color:var(--navy)"><use href="#icon-tick"/></svg>Lorem ipsum dolor</td><td><svg style="color:var(--navy)"><use href="#icon-tick"/></svg>Lorem ipsum dolor</td></tr>
      <tr><td><svg style="color:var(--navy)"><use href="#icon-tick"/></svg>Lorem ipsum dolor</td><td class="is-featured"><svg style="color:var(--navy)"><use href="#icon-tick"/></svg>Lorem ipsum dolor</td><td><svg style="color:var(--navy)"><use href="#icon-tick"/></svg>Lorem ipsum dolor</td></tr>
      <tr><td></td><td class="is-featured"><svg style="color:var(--navy)"><use href="#icon-tick"/></svg>Lorem ipsum dolor</td><td></td></tr>
    </tbody>
  </table>
  <p class="body-text body-text--indent" style="top:183px">Lorem ipsum dolor sit amet, consetetur sadipscing elitr, sed diam nonumy eirmod tempor invidunt ut labore et dolore magna aliquyam erat, sed diam voluptua. Stet clita kasd gubergren, no sea takimata sanctus est Lorem ipsum dolor sit amet.</p>
  <p class="body-text" style="top:238px">At vero eos et accusam et justo duo dolores et ea rebum. Stet clita kasd gubergren, no sea takimata. Stet clita kasd gubergren, no sea takimata sanctus est Lorem ipsum dolor sit amet.</p>
  <footer class="footer">
    <svg class="footer__wave" width="500" height="375"><use href="#footer-wave"/></svg>
    <p class="footer__address">Lorem Ipsum Street 122<br>State, Country<br>Phone&nbsp; 0123 4567 89</p>
    <span class="footer__link footer__link--web"><span class="dot" style="color:var(--navy)"><svg><use href="#icon-home"/></svg></span>company-name.com</span>
    <span class="footer__link footer__link--page"><span class="dot"></span>linkpage.net/company-name</span>
    <span class="footer__link footer__link--chirp"><span class="dot"></span>chirpnet.net/company-name</span>
    <span class="footer__link footer__link--mail"><span class="dot" style="color:var(--navy)"><svg><use href="#icon-at"/></svg></span>hello@company-name.com</span>
    <span class="footer__link footer__link--video"><span class="dot"></span>vidhub.net/company-name</span>
    <div class="footer__brand"><span class="mark"></span>quantrel</div>
    <div class="pager"><span class="pager__btn" style="color:#fff"><svg><use href="#icon-caret-left"/></svg></span><span>8 <span class="pager__of">of</span> 13</span><span class="pager__btn" style="color:#fff"><svg><use href="#icon-caret-right"/></svg></span></div>
  </footer>
</section>

</body>
</html>
```